Wordpress Design Project - Leadership Guide Nest

Website Brief

We are looking to have a design produced for a modern professional website. A mind map of the site can be found here: http://www.thoughtlattice.example/view.htm?m=58142736a1b94c07d2e5f8a3c6b71d09

Each of the green tabs are pages just next to them is a very small green globe. If you click this. It will take you through to an example page for that section.

Task description
The website will be made up of:
1. A homepage (this will be the blog see http://www.janetquillby.example for an example of the crisp and cleanness we are looking for)
2. A page that will have just a video and option page (see: http://tvpgacademy.example/ for example)
3. 3 pages all with the same structure. (see: http://tvpgacademy.example/qw72plx19bnv/ for an example). Each will have:
a. A video
b. Tabs at the top of the video that link to the 3 videos and the sales page
c. Link to a resource download
d. Facebook Comments section
4. 2 Page with about the experts and about our company (same style for both)
5. A page that will have a long well designed sales page (see: http://tvpgacademy.example/early-enrollment-2013/ for an example)
6. A page with testimonials on it (see http://www.janetquillby.example/praise/)
7. A page that will describe the products, services and provision we will be offering
8. A page that will detail our involvement with charities and not for profits

Must Have
Edgey, crisp design, similar to Janet Quillbys. We would like the colours to match very well throughout the site and have a unique font (possibly manksans). We want it to have very clean integrations between copy and images with shadows on videos for example like with Janetquillbys page. We really love this design and would like this to be the inspiration for our site however it would need to certainly have a more executive feel to suit our target market.

We like the idea of some kind of circles, crisp clean lines, nice white space, simple design, corporate looking, communicates wealth/success/massive value. Based on the two logos of NDLTR and the Hub (see attached)

Target Market:
The target market includes intelligent, productive coaches, who are self employed or part of small firms. They are well educated, well read, socially conscious, and committed to making a profound difference with their clients...skilled at the actions of coaching, but not the business side. There will be a ratio of approximately 60% male / 40% female (really? The coaching industry is predominantly female, no?), with an age range of 40 to 60 years. English is our core language. Most will have secondary education and the salary range will be $90,000 to $400,000. We will have a global audience reach, although the primary markets will be North America, Europe and Australia/NZ.

Marketing Objective:
LGN will be an on-line resource for Executive Coaches. The intent of the design will be to present LGN to the world as a highly professional organization. The intent is not to characterize LGN as solely corporate, but will also incorporate elements of entrepreneurialism. We require the brand to incorporate these values:
• Trustworthy – you can trust us
• Professional – we are true professionals whose mission is to provide value to our clients
• Caring - Interested in our clients wellbeing – we are keenly interested in helping our clients build their knowledge, skills, and attitudes to be highly productive and successful
• Successful
• Knowledgeable – we have breadth and depth of knowledge in leadership
• World-class – we have a world-wide target market and, as such, need the brand to reflect a powerful and inclusive image
• Positive Energy - I would like the brand to have positive energy and very clean feng shui
• Prestige
• Massive Value
• Accessible
• Worldly/ Sophisticated
• Affordable
• Mission-critical

Details about the needs, wants, aspirations etc. of our target market
Executive coaches need a process and a system for creating opportunities to do the work they love with clients who are qualified to engage them and pay them. There is a scarcity mentality around their own finances, but ironically an abundance mentality for what's possible in the world and for their clients. They want to make a difference, they want to facilitate transformation, they want to be of deep service.

They aspire to make a decent living doing it! They need help bridging the gap between practitioner/service provider and financially successful entrepreneur/business owner/ leader. They also aspire to have it be easy, as it feels hard for them to generate the revenues they want to generate solely through coaching, so many turn to training, speaking, and other revenue streams.

Required assets to send through to web designer
1. Three blog posts. Each will have:
a. A video/audio
b. Summary of the points raised
c. Download (possibly slides)
2. A page that will have just a video and option page
a. Headline
b. Video
c. One paragraph summary of what we do
3. 3 launch videos. Here for each we will need
a. A video scripted and produced
b. Title for each
c. A resource download
4. Sales page
a. Video
b. Copy
i. Overview
ii. Content of course
iii. Guarentee
iv. Details of bonuses
v. Details of support
vi. Pricing broken down ($30,000 value = $2000)
c. Animated Gif
5. About the company and experts
a. Description of our company, it's vision, mission, purpose and core values.
b. Description of each of us,
i. our key facts and wows,
ii. a picture of us
iii. some interesting facts (giving personality)
iv. Lower down we will add in "Faculty" these will be any thought leaders we invite in to be part of the value delivery (will add to our credibility having such a strong team behind the project)
6. Testimonials
a. Testimonials from coaches from working with us
7. Products, services and provision we will be offering
a. A simple description of each of the key products/services we will be offering
i. Leadership Guide Sales
ii. Leadership Guide Marketing
iii. Leadership Guide Help
iv. Leadership Guide Roundtable
v. Leadership Guide Resources
a. List of the various charity work each of us have been involved with

Requirements
Must have
• Edgey, crisp design, similar to Janet Quillbys. We would like the colours to match very well throughout the site and have a unique font (possibly manksans). We want it to have very clean integrations between copy and images with shadows on videos for example like with Janetquillbys page. We really love this design and would like this to be the inspiration for our site however it would need to certainly have a more executive feel to suit our target market.

```html
<!DOCTYPE html>
<html lang="en">
<head>
<meta charset="utf-8">
<title>Leadership Guide Nest — Blog</title>
<link href="https://fonts.googleapis.com/css2?family=Open+Sans:wght@300;400;600;700&display=swap" rel="stylesheet">
<style>
:root{
  --orange:#f39a1e;
  --orange-deep:#e07f0c;
  --orange-light:#f8c069;
  --ink:#3a3a3a;
  --muted:#8a8a8a;
  --rule:#e2e2e2;
  --nav:#5b5b5b;
  --footer:#303030;
  --footer-base:#1e1e1e;
  --paper:#ffffff;
  --link:#c7771a;
}
*{box-sizing:border-box;margin:0;padding:0}
html,body{width:683px;height:1200px;overflow:hidden}
body{background:var(--paper);font-family:"Open Sans",Arial,sans-serif;color:var(--ink);position:relative;font-size:7px;line-height:1.45}

/* Header */
.site-header{position:absolute;left:0;top:0;width:683px;height:90px}
.brand{position:absolute;left:28px;top:26px;display:flex;align-items:center;gap:7px}
.brand-mark{width:26px;height:26px;border-radius:50%;background:var(--orange)}
.brand-name{font-size:14px;font-weight:600;color:#6d6d6d;letter-spacing:-.2px}
.register{position:absolute;left:424px;top:38px;display:flex;align-items:center;gap:5px}
.register-label{font-size:11px;color:#666;margin-right:2px}
.field{height:15px;border:1px solid #cfcfcf;font-size:6px;color:#999;padding:3px 4px;background:#fff}
.field.short{width:58px}
.field.long{width:72px}
.go-btn{width:15px;height:15px;background:#222;display:flex;align-items:center;justify-content:center}

/* Navigation */
.main-nav{position:absolute;left:0;top:91px;width:683px;height:17px;background:var(--nav)}
.main-nav ul{list-style:none;display:flex;gap:19px;padding-left:82px;height:100%;align-items:center}
.main-nav a{color:#fff;text-decoration:none;font-size:6.5px;font-weight:600;letter-spacing:.3px}

/* Hero slider */
.hero{position:absolute;left:0;top:108px;width:683px;height:190px;background:linear-gradient(90deg,var(--orange-deep),var(--orange) 35%,var(--orange-light) 60%,var(--orange) 85%,var(--orange-deep))}
.hero-photo{position:absolute;left:80px;top:0;width:523px;height:190px;background:linear-gradient(90deg,#b96c1c 0%,#d9a15a 30%,#efe3cf 55%,#d7c2a2 75%,#c98b3c 100%)}
.slide-arrow{position:absolute;top:85px;width:18px;height:18px;background:rgba(120,120,120,.85);display:flex;align-items:center;justify-content:center}
.slide-arrow.prev{left:0}
.slide-arrow.next{right:0}

/* Main column */
.post{position:absolute;left:80px;top:304px;width:352px}
.post-title{font-size:9.5px;font-weight:600;line-height:1.3;color:#333}
.post-meta{font-size:5.5px;color:var(--muted);margin-top:3px}
.post-image{margin-top:9px;width:352px;height:178px;background:radial-gradient(circle at 55% 40%,#f0c9a5,#d58b3f 55%,#b86a22)}
.post-body{margin-top:8px;font-size:5.8px;color:#555;line-height:1.55}
.post-body p+p{margin-top:5px}
.video{margin-top:8px;width:352px;height:300px;position:relative;box-shadow:0 3px 8px rgba(0,0,0,.35)}
.video-frame{position:absolute;inset:0 0 22px 0;background:linear-gradient(180deg,#6d7079,#9d8f86 50%,#4a4b52)}
.video-play{position:absolute;left:158px;top:122px;width:36px;height:36px;border-radius:50%;background:rgba(20,20,20,.75);display:flex;align-items:center;justify-content:center}
.video-bar{position:absolute;left:0;right:0;bottom:0;height:22px;background:#1b1b1b;display:flex;align-items:center;gap:7px;padding:0 8px}
.video-track{flex:1;height:3px;background:#555;position:relative}
.video-track span{position:absolute;left:0;top:0;height:3px;width:22%;background:#d8d8d8}
.read-more{display:block;margin-top:9px;font-size:5.5px;color:var(--link);font-weight:600;text-decoration:none}
.share-row{display:flex;justify-content:center;gap:5px;margin-top:2px}
.share-chip{width:22px;height:9px;border:1px solid #cfcfcf;border-radius:2px;background:#f4f4f4}
.pager{margin-top:20px;display:flex;gap:8px;font-size:6px;color:#777}

/* Sidebar */
.sidebar{position:absolute;left:446px;top:304px;width:157px}
.side-heading{font-size:6.5px;font-weight:600;color:#555;letter-spacing:.3px;border-bottom:1px solid var(--rule);padding-bottom:3px}
.download-btn{margin-top:17px;height:34px;background:linear-gradient(180deg,#fbc23d,#f29a14);display:flex;align-items:center;padding-left:8px;gap:8px;font-size:15px;font-weight:700;color:#3a3a3a}
.download-arrow{width:26px;height:20px;background:#333;border-radius:2px;display:flex;align-items:center;justify-content:center}
.resource-box{margin-top:10px;border:1px solid var(--rule);padding:8px 7px 4px}
.box-brand{display:flex;align-items:center;gap:5px;padding-bottom:7px;border-bottom:1px solid var(--rule)}
.box-brand .brand-mark{width:14px;height:14px}
.box-brand .brand-name{font-size:8px}
.resource-item{display:flex;gap:6px;padding:6px 0;border-bottom:1px solid #eee}
.resource-item:last-child{border-bottom:0}
.thumb{width:26px;height:26px;flex:none;background:linear-gradient(135deg,#7d6e62,#c9b6a3)}
.resource-text{font-size:5.4px;line-height:1.35;color:#555}
.resource-text .date{color:var(--muted);font-size:4.8px;margin-top:1px}
.testimonials{margin-top:11px}
.quote{margin-top:6px;font-size:5.6px;color:#666;line-height:1.55}
.client{margin-top:5px;font-size:5.5px;color:#444;font-weight:600}
.view-all{display:block;margin-top:10px;text-align:right;font-size:5px;color:var(--muted);text-decoration:none;letter-spacing:.3px}

/* Footer */
.footer-main{position:absolute;left:0;top:980px;width:683px;height:182px;background:var(--footer)}
.footer-video{position:absolute;left:80px;top:22px;width:216px;height:146px;background:linear-gradient(160deg,#3c4a5c,#6b6259 55%,#2a2a2a)}
.footer-video .video-play{left:90px;top:55px}
.signup{position:absolute;left:353px;top:44px}
.signup h2{font-size:19px;font-weight:300;color:#fff;letter-spacing:-.2px}
.signup-fields{display:flex;gap:5px;margin-top:10px;align-items:center}
.signup-fields .field{background:#fff;width:96px;height:13px;font-size:5.5px;padding:2px 4px;border:0}
.signup-fields .go-btn{width:13px;height:13px;background:#111}
.connect{display:flex;align-items:center;gap:5px;margin-top:26px;font-size:9px;color:#ddd}
.social{width:10px;height:10px;background:#6f86b5;border-radius:1px}
.social.alt{background:#56a5d6}
.social.third{background:#8a8a8a}
.footer-base{position:absolute;left:0;top:1162px;width:683px;height:38px;background:var(--footer-base);display:flex;align-items:center;justify-content:space-between;padding:0 80px}
.footer-links{display:flex;gap:14px;list-style:none}
.footer-links a{color:#aaa;font-size:5.5px;text-decoration:none;letter-spacing:.3px}
.copyright{font-size:5px;color:#888}
</style>
</head>
<body>

<header class="site-header">
  <div class="brand">
    <span class="brand-mark"></span>
    <span class="brand-name">LeadershipGuideNest.com</span>
  </div>
  <form class="register">
    <span class="register-label">Register Now</span>
    <span class="field short">First name</span>
    <span class="field long">Email</span>
    <span class="go-btn"><svg width="6" height="6" viewBox="0 0 6 6"><path d="M1 0l4 3-4 3z" fill="#fff"/></svg></span>
  </form>
</header>

<nav class="main-nav">
  <ul>
    <li><a href="#">HOME</a></li>
    <li><a href="#">ABOUT</a></li>
    <li><a href="#">WORK WITH US</a></li>
    <li><a href="#">TESTIMONIALS</a></li>
    <li><a href="#">GIVING BACK</a></li>
    <li><a href="#">BLOG</a></li>
    <li><a href="#">CONTACT</a></li>
  </ul>
</nav>

<section class="hero">
  <div class="hero-photo" role="img" aria-label="Photograph of a coach in conversation with a client in a bright office"></div>
  <span class="slide-arrow prev"><svg width="8" height="10" viewBox="0 0 8 10"><path d="M7 0L0 5l7 5z" fill="#fff"/></svg></span>
  <span class="slide-arrow next"><svg width="8" height="10" viewBox="0 0 8 10"><path d="M1 0l7 5-7 5z" fill="#fff"/></svg></span>
</section>

<main class="post">
  <h1 class="post-title">Lorem ipsum dolor sit amet, consectetur adipiscing elit. Nulla sodales ipsum quis metus...</h1>
  <p class="post-meta">By administrator — On Dec 26, 2012</p>
  <div class="post-image" role="img" aria-label="Portrait photograph of a smiling executive coach"></div>
  <div class="post-body">
    <p>Lorem ipsum dolor sit amet, consectetur adipiscing elit. Nulla sodales ipsum quis metus tristique vestibulum vel eleifend ligula. Donec quis tellus venenatis turpis porta pretium in eget nisi. Mauris consequat erat nibh, vitae vulputate tincidunt sit nec purus. Quisque cursus risus non sapien hendrerit interdum vitae nisl. Morbi fringilla tortor. Donec id tortor vitae urna ultricies pulvinar sit at amet eget. Aenean venenatis, lorem sed sagittis pretium, neque sem commodo arcu.</p>
    <p>Lorem ipsum dolor sit amet, consectetur adipiscing elit. Nulla sodales ipsum quis metus tristique vestibulum vel eleifend ligula. Donec quis tellus venenatis turpis porta pretium in eget nisi. Mauris consequat erat nibh, vitae vulputate tincidunt sit nec purus. Quisque cursus risus non sapien hendrerit interdum vitae nisl. Morbi fringilla tortor. Donec id tortor vitae urna ultricies pulvinar sit at amet eget. Aenean venenatis, lorem sed sagittis pretium, neque sem commodo arcu.</p>
  </div>
  <div class="video">
    <div class="video-frame" role="img" aria-label="Video still of a speaker addressing the camera"></div>
    <span class="video-play"><svg width="14" height="16" viewBox="0 0 14 16"><path d="M2 0l12 8-12 8z" fill="#fff"/></svg></span>
    <div class="video-bar">
      <svg width="7" height="8" viewBox="0 0 7 8"><path d="M0 0l7 4-7 4z" fill="#ddd"/></svg>
      <div class="video-track"><span></span></div>
      <svg width="9" height="8" viewBox="0 0 9 8"><path d="M0 2h3l3-2v8L3 6H0z" fill="#ddd"/></svg>
      <svg width="8" height="8" viewBox="0 0 8 8"><path d="M0 0h3v1H1v2H0zM8 0v3H7V1H5V0zM0 8V5h1v2h2v1zM8 8H5V7h2V5h1z" fill="#ddd"/></svg>
    </div>
  </div>
  <a class="read-more" href="#">READ MORE</a>
  <div class="share-row">
    <span class="share-chip"></span><span class="share-chip"></span><span class="share-chip"></span><span class="share-chip"></span>
  </div>
  <div class="pager"><span>« Previous</span><span>Next »</span></div>
</main>

<aside class="sidebar">
  <h3 class="side-heading">RESOURCES</h3>
  <a class="download-btn">DOWNLOAD <span class="download-arrow"><svg width="14" height="10" viewBox="0 0 14 10"><path d="M0 3h8V0l6 5-6 5V7H0z" fill="var(--orange)"/></svg></span></a>
  <div class="resource-box">
    <div class="box-brand"><span class="brand-mark"></span><span class="brand-name">LeadershipGuideNest.com</span></div>
    <div class="resource-item"><span class="thumb" role="img" aria-label="Thumbnail photo for article"></span><div class="resource-text">Sed nisi. Mauris consequat erat nibh, vitae vulputate tincidunt sit nec purus.<div class="date">By administrator — December 26, 2012</div></div></div>
    <div class="resource-item"><span class="thumb" role="img" aria-label="Thumbnail photo for article"></span><div class="resource-text">Sed nisi. Mauris consequat erat nibh, vitae vulputate tincidunt sit nec purus.<div class="date">By administrator — December 26, 2012</div></div></div>
    <div class="resource-item"><span class="thumb" role="img" aria-label="Thumbnail photo for article"></span><div class="resource-text">Sed nisi. Mauris consequat erat nibh, vitae vulputate tincidunt sit nec purus.<div class="date">By administrator — December 26, 2012</div></div></div>
    <div class="resource-item"><span class="thumb" role="img" aria-label="Thumbnail photo for article"></span><div class="resource-text">Sed nisi. Mauris consequat erat nibh, vitae vulputate tincidunt sit nec purus.<div class="date">By administrator — December 26, 2012</div></div></div>
  </div>
  <section class="testimonials">
    <h3 class="side-heading">TESTIMONIALS</h3>
    <p class="quote">“Lorem ipsum dolor sit amet, consectetur adipiscing elit. Nulla sodales ipsum quis metus tristique vestibulum vel eleifend ligula. Donec quis tellus venenatis turpis porta pretium in eget nisi. Morbi fringilla tortor donec.”</p>
    <p class="client">NAME OF THE CLIENT</p>
    <a class="view-all" href="#">VIEW ALL TESTIMONIALS</a>
  </section>
</aside>

<footer>
  <div class="footer-main">
    <div class="footer-video" role="img" aria-label="Video still of the two company founders">
      <span class="video-play"><svg width="14" height="16" viewBox="0 0 14 16"><path d="M2 0l12 8-12 8z" fill="#fff"/></svg></span>
    </div>
    <div class="signup">
      <h2>Create an account</h2>
      <div class="signup-fields">
        <span class="field">First name</span>
        <span class="field">Email</span>
        <span class="go-btn"><svg width="6" height="6" viewBox="0 0 6 6"><path d="M1 0l4 3-4 3z" fill="#fff"/></svg></span>
      </div>
      <div class="connect">Connect with us <span class="social"></span><span class="social alt"></span><span class="social third"></span></div>
    </div>
  </div>
  <div class="footer-base">
    <ul class="footer-links">
      <li><a href="#">ABOUT</a></li>
      <li><a href="#">WORK WITH US</a></li>
      <li><a href="#">TESTIMONIALS</a></li>
      <li><a href="#">GIVING BACK</a></li>
      <li><a href="#">CONTACT</a></li>
    </ul>
    <p class="copyright">© 2013 LeadershipGuideNest.com. All Rights Reserved.</p>
  </div>
</footer>

</body>
</html>
```